KPL Construction we build lodges in Botswana

We need a Design Layout only with Categories where we can update each projects photos.... We have a web address and a host - kpl.construction

```html
<!DOCTYPE html>
<html lang="en">
<head>
<meta charset="utf-8">
<title>KPL Construction</title>
<link href="https://fonts.googleapis.com/css2?family=Montserrat:wght@500;600;700&family=Open+Sans:wght@400;600&display=swap" rel="stylesheet">
<style>
:root{
  --red:#e8212e;
  --red-dark:#c4141f;
  --ink:#2b2b2b;
  --muted:#6b6b6b;
  --grey:#eeeeee;
  --white:#ffffff;
  --line:#d9d9d9;
}
*{box-sizing:border-box;margin:0;padding:0}
html,body{width:1200px;height:4032px;overflow:hidden}
body{font-family:"Open Sans",sans-serif;color:var(--ink);background:var(--white);position:relative}
h1,h2,h3,.nav a,.btn{font-family:"Montserrat",sans-serif}
.abs{position:absolute}

/* top bar */
.topbar{position:absolute;top:0;left:0;width:1200px;height:48px;background:var(--red);display:flex;align-items:center;justify-content:space-between;padding:0 90px;color:#fff;font-size:15px}
.social{display:flex;gap:12px}
.social span{width:18px;height:18px;border-radius:50%;background:rgba(255,255,255,.85);display:block}
.contact-mini{display:flex;gap:28px;align-items:center;white-space:nowrap}
.contact-mini svg{width:16px;height:16px;vertical-align:-3px;margin-right:6px}

/* header */
.header{position:absolute;top:48px;left:0;width:1200px;height:104px;display:flex;align-items:center;justify-content:space-between;padding:0 90px}
.brand{font-family:"Montserrat",sans-serif;color:var(--ink);font-weight:600;font-size:32px;white-space:nowrap;display:flex;align-items:center;gap:12px}
.brand-mark{width:18px;height:18px;background:var(--red);display:block}
.nav{display:flex;gap:36px;white-space:nowrap}
.nav a{color:var(--ink);text-decoration:none;font-size:16px;font-weight:500}

/* hero */
.hero{position:absolute;top:152px;left:0;width:1200px;height:700px;background:linear-gradient(180deg,#1b1a18 0%,#3a2f24 45%,#5b4634 75%,#2a241f 100%)}
.hero-text{position:absolute;top:255px;left:0;width:1200px;text-align:center;color:#fff}
.hero-text h1{font-size:52px;font-weight:600;letter-spacing:1px}
.hero-text p{font-size:22px;line-height:30px;margin-top:12px}
.btn{display:inline-flex;align-items:center;gap:10px;background:var(--red);color:#fff;font-weight:600;font-size:17px;padding:14px 38px;border-radius:28px;text-decoration:none}
.hero .btn{margin-top:24px}

/* about */
.about-frame{position:absolute;left:60px;top:940px;width:482px;height:332px;border:3px dashed var(--red)}
.about-img{position:absolute;left:80px;top:960px;width:452px;height:300px;background:linear-gradient(135deg,#4b2c18,#a9652e 55%,#3b2214)}
.about-text{position:absolute;left:568px;top:968px;width:550px}
.about-text h2{color:var(--red);font-size:36px;font-weight:600;margin-bottom:18px}
.about-text p{font-size:16px;line-height:26px;color:var(--muted)}
.about-text .btn{margin-top:26px}

/* offer */
.offer{position:absolute;top:1370px;left:0;width:1200px;height:910px;background:linear-gradient(180deg,#7c8791 0%,#6b7178 40%,#5e6a5e 70%,#8a7a6a 100%)}
.offer-head{position:absolute;top:112px;left:0;width:1200px;text-align:center}
.offer-head h2{color:var(--red);font-size:38px;font-weight:600}
.offer-head p{color:#fff;font-size:15px;line-height:24px;margin:16px auto 0;width:760px}
.mission{position:absolute;left:96px;top:282px;width:320px;height:620px;background:#fff}
.mission-img{width:320px;height:300px;background:linear-gradient(160deg,#c9b08a,#8c6c47 60%,#5e4a35)}
.mission h3{color:var(--red);font-size:30px;font-weight:600;padding:22px 24px 10px}
.mission p{font-size:15px;line-height:23px;color:var(--muted);padding:0 24px}
.mission .btn{position:absolute;left:0;bottom:0;width:320px;border-radius:0;justify-content:center;font-size:15px;padding:14px 0}
.service{position:absolute;width:308px;background:#fff;text-align:center;padding:36px 16px 0;height:270px}
.service .ico{width:56px;height:56px;margin:0 auto 14px;display:block}
.service h3{color:var(--red);font-size:18px;font-weight:600;margin-bottom:12px;white-space:nowrap}
.service p{font-size:13px;line-height:20px;color:var(--muted)}
.service .more{display:block;margin-top:16px;color:var(--red);font-size:14px;font-weight:600;font-family:"Montserrat",sans-serif}

/* projects */
.projects{position:absolute;top:2280px;left:0;width:1200px;height:760px;background:var(--grey)}
.projects h2{position:absolute;top:100px;width:1200px;text-align:center;color:var(--red);font-size:38px;font-weight:600}
.tile{position:absolute;width:308px;height:200px}

/* contact */
.info{position:absolute;top:3150px;width:360px;text-align:center;font-size:17px;line-height:26px;color:var(--ink)}
.info .circle{width:76px;height:76px;border-radius:50%;background:var(--red);margin:0 auto 22px;display:flex;align-items:center;justify-content:center}
.form{position:absolute;left:168px;top:3316px;width:864px;display:grid;grid-template-columns:1fr 1fr;column-gap:16px}
.field{height:46px;border:1px solid var(--line);font-size:14px;color:#777;padding:0 14px;display:flex;align-items:center;margin-bottom:4px}
.field.tall{height:192px;align-items:flex-start;padding-top:13px}
.submit{position:absolute;left:512px;top:3532px;width:176px;height:44px;background:var(--red);color:#fff;font-family:"Montserrat",sans-serif;font-weight:600;font-size:16px;display:flex;align-items:center;justify-content:center}

/* footer */
.footer{position:absolute;top:3620px;left:0;width:1200px;height:412px;background:linear-gradient(180deg,#e4414a,#d83a40 60%,#c8323a)}
.footer .f-brand{position:absolute;top:174px;width:1200px;text-align:center;color:#fff;font-family:"Montserrat",sans-serif;font-size:46px;font-weight:600}
.f-social{position:absolute;top:250px;width:1200px;display:flex;justify-content:center;gap:12px}
.f-social span{width:38px;height:38px;border-radius:50%;border:2px solid #fff;display:block}
.f-nav{position:absolute;top:310px;width:1200px;display:flex;justify-content:center;gap:26px;color:#fff;font-family:"Montserrat",sans-serif;font-size:16px;font-weight:600}
.copy{position:absolute;top:350px;width:1200px;text-align:center;color:#fff;font-size:13px}
</style>
</head>
<body>

<div class="topbar">
  <div class="social"><span></span><span></span><span></span><span></span><span></span><span></span></div>
  <div class="contact-mini">
    <span><svg viewBox="0 0 16 16"><rect x="1" y="3" width="14" height="10" fill="none" stroke="#fff" stroke-width="1.6"/><path d="M1 3l7 6 7-6" fill="none" stroke="#fff" stroke-width="1.6"/></svg>Email us info@kpl.construction</span>
    <span><svg viewBox="0 0 16 16"><path d="M3 1l3 3-2 2c1 2 3 4 5 5l2-2 3 3-2 3C7 15 1 9 1 3z" fill="#fff"/></svg>Call us +267 390 1234</span>
  </div>
</div>

<header class="header">
  <div class="brand"><span class="brand-mark"></span>KPL Construction</div>
  <nav class="nav"><a>Home</a><a>Project</a><a>About Us</a><a>Testimonials</a><a>Blog</a><a>Contact Us</a></nav>
</header>

<section class="hero" role="img" aria-label="Evening photo of a safari lodge deck with lanterns and seating">
  <div class="hero-text">
    <h1>WELCOME TO KPL CONSTRUCTION</h1>
    <p>Sed ut perspiciatis unde omnis iste natus error sit voluptatem<br>veritatis et quasi architecto</p>
    <a class="btn"><svg width="18" height="18" viewBox="0 0 16 16"><path d="M1 8l14-6-5 13-2-5z" fill="#fff"/></svg>Contact us</a>
  </div>
</section>
<svg class="abs" style="top:760px;left:0" width="1200" height="110" viewBox="0 0 1200 110">
  <polygon points="0,20 600,92 1200,20 1200,110 0,110" fill="#fff"/>
  <polyline points="0,20 600,92 1200,20" fill="none" stroke="#e8212e" stroke-width="6"/>
</svg>

<div class="about-frame"></div>
<div class="about-img" role="img" aria-label="Photo of a lodge bedroom interior lit by a fireplace"></div>
<div class="about-text">
  <h2>ABOUT US</h2>
  <p>Sed ut perspiciatis unde omnis iste natus error sit voluptatem accusantium doloremque laudantium, totam rem aperiam, eaque ipsa quae ab illo inventore veritatis et quasi architecto beatae vitae dicta sunt explicabo. Nemo enim ipsam voluptatem quia voluptas sit aspernatur aut odit aut fugit, sed quia consequuntur magni dolores eos qui ratione voluptatem sequi nesciunt.</p>
  <a class="btn"><svg width="16" height="16" viewBox="0 0 16 16"><rect x="2" y="2" width="12" height="12" fill="none" stroke="#fff" stroke-width="2"/><path d="M5 6h6M5 10h6" stroke="#fff" stroke-width="2"/></svg>Read More</a>
</div>

<section class="offer" role="img" aria-label="Tinted photo of a thatched lodge among trees">
  <div class="offer-head">
    <h2>WHAT WE OFFER</h2>
    <p>Aenean sollicitudin, lorem quis bibendum auctor, nisi elit consequat ipsum, nec nibh id elit. Duis sed odio sit amet nibh vulputate cursus a sit amet mauris. Morbi accumsan ipsum velit.</p>
  </div>
  <div class="mission">
    <div class="mission-img" role="img" aria-label="Photo of guests seated on a lodge deck overlooking the bush"></div>
    <h3>OUR MISSION</h3>
    <p>Sed ut perspiciatis unde omnis iste natus error sit voluptatem accusantium doloremque laudantium, totam rem aperiam, eaque ipsa quae ab illo inventore veritatis et quasi architecto beatae vitae dicta sunt explicabo.</p>
    <a class="btn"><svg width="16" height="16" viewBox="0 0 16 16"><path d="M8 1v10M4 7l4 4 4-4M2 14h12" stroke="#fff" stroke-width="2" fill="none"/></svg>Download brochure</a>
  </div>
  <div class="service" style="left:460px;top:302px">
    <svg class="ico" viewBox="0 0 56 56"><rect x="10" y="10" width="36" height="36" fill="none" stroke="#e8212e" stroke-width="3"/><path d="M10 22h36M22 22v24" stroke="#e8212e" stroke-width="3"/></svg>
    <h3>DESIGN</h3>
    <p>Lodge layouts drawn to suit the site. Proin gravida nibh vel velit auctor aliquet. Aenean sollicitudin lorem quis.</p>
    <span class="more">Read More ›</span>
  </div>
  <div class="service" style="left:792px;top:302px">
    <svg class="ico" viewBox="0 0 56 56"><path d="M8 46h40M14 46V24l14-12 14 12v22" fill="none" stroke="#e8212e" stroke-width="3"/><rect x="24" y="32" width="8" height="14" fill="#e8212e"/></svg>
    <h3>PLANNING</h3>
    <p>Clear schedules from first sketch to handover. Proin gravida nibh vel velit auctor aliquet. Aenean sollicitudin.</p>
    <span class="more">Read More ›</span>
  </div>
  <div class="service" style="left:460px;top:610px">
    <svg class="ico" viewBox="0 0 56 56"><rect x="8" y="10" width="40" height="28" fill="none" stroke="#e8212e" stroke-width="3"/><circle cx="28" cy="40" r="7" fill="#e8212e"/><path d="M16 20h24M16 27h16" stroke="#e8212e" stroke-width="3"/></svg>
    <h3>CERTIFICATION</h3>
    <p>Every build checked against local standards. Proin gravida nibh vel velit auctor aliquet. Aenean sollicitudin.</p>
    <span class="more">Read More ›</span>
  </div>
  <div class="service" style="left:792px;top:610px">
    <svg class="ico" viewBox="0 0 56 56"><rect x="10" y="8" width="20" height="40" fill="#e8212e"/><rect x="32" y="20" width="14" height="28" fill="none" stroke="#e8212e" stroke-width="3"/></svg>
    <h3>CONSTRUCTION SERVICES</h3>
    <p>Skilled crews building lodges across Botswana. Proin gravida nibh vel velit auctor aliquet. Aenean sollicitudin.</p>
    <span class="more">Read More ›</span>
  </div>
</section>
<svg class="abs" style="top:1352px;left:0" width="1200" height="90" viewBox="0 0 1200 90">
  <polygon points="0,0 1200,0 1200,62 600,20 0,62" fill="#fff"/>
  <polyline points="0,62 600,20 1200,62" fill="none" stroke="#e8212e" stroke-width="6"/>
</svg>

<section class="projects">
  <h2>OUR PROJECTS</h2>
  <div class="tile" style="left:120px;top:188px;background:linear-gradient(135deg,#3c2414,#9a5a2a)" role="img" aria-label="Project photo: lodge interior by firelight"></div>
  <div class="tile" style="left:440px;top:188px;background:linear-gradient(180deg,#6d93c2,#4f6a3a)" role="img" aria-label="Project photo: thatched lodge under blue sky"></div>
  <div class="tile" style="left:768px;top:188px;background:linear-gradient(180deg,#7ea3cf,#8a7450)" role="img" aria-label="Project photo: lodge boma and fire pit"></div>
  <div class="tile" style="left:120px;top:400px;background:linear-gradient(135deg,#1f2a3a,#6a4a2c)" role="img" aria-label="Project photo: lodge terrace at dusk"></div>
  <div class="tile" style="left:440px;top:400px;background:linear-gradient(180deg,#8fb0d0,#7a6440)" role="img" aria-label="Project photo: lodge units with walkways"></div>
  <div class="tile" style="left:768px;top:400px;background:linear-gradient(180deg,#5f7c3c,#34482a)" role="img" aria-label="Project photo: lodge rooms among trees"></div>
</section>
<svg class="abs" style="top:2930px;left:0" width="1200" height="150" viewBox="0 0 1200 150">
  <polygon points="0,10 600,120 1200,10 1200,150 0,150" fill="#fff"/>
  <polyline points="0,10 600,120 1200,10" fill="none" stroke="#e8212e" stroke-width="6"/>
</svg>

<div class="info" style="left:140px">
  <div class="circle"><svg width="36" height="36" viewBox="0 0 24 24"><path d="M12 2a7 7 0 0 0-7 7c0 5 7 13 7 13s7-8 7-13a7 7 0 0 0-7-7z" fill="none" stroke="#fff" stroke-width="2"/><circle cx="12" cy="9" r="2.5" fill="#fff"/></svg></div>
  14 Kgale View Rd,<br>Gaborone, Botswana
</div>
<div class="info" style="left:420px">
  <div class="circle"><svg width="34" height="34" viewBox="0 0 16 16"><path d="M3 1l3 3-2 2c1 2 3 4 5 5l2-2 3 3-2 3C7 15 1 9 1 3z" fill="none" stroke="#fff" stroke-width="1.4"/></svg></div>
  Phone: +267 390 1234<br>Fax: +267 390 1235
</div>
<div class="info" style="left:700px">
  <div class="circle"><svg width="36" height="36" viewBox="0 0 24 24"><rect x="3" y="6" width="18" height="12" fill="none" stroke="#fff" stroke-width="2"/><path d="M3 6l9 7 9-7" fill="none" stroke="#fff" stroke-width="2"/></svg></div>
  Email: hello@kpl.construction<br>Support: help@kpl.construction
</div>

<form class="form">
  <div>
    <div class="field">First Name</div>
    <div class="field">Address</div>
    <div class="field">Email Address</div>
    <div class="field">Phone Number</div>
  </div>
  <div>
    <div class="field">Last Name</div>
    <div class="field tall">Message</div>
  </div>
</form>
<div class="submit">Submit</div>

<footer class="footer" role="img" aria-label="Red tinted aerial photo of a lodge complex">
  <div class="f-brand">KPL Construction</div>
  <div class="f-social"><span></span><span></span><span></span><span></span><span></span></div>
  <div class="f-nav"><span>HOME</span><span>|</span><span>ABOUT US</span><span>|</span><span>TESTIMONIALS</span><span>|</span><span>PROJECTS</span><span>|</span><span>BLOG</span><span>|</span><span>CONTACT</span></div>
  <div class="copy">Copyright © 2024 KPL Construction</div>
</footer>
<svg class="abs" style="top:3600px;left:0" width="1200" height="80" viewBox="0 0 1200 80">
  <polygon points="0,0 1200,0 1200,56 600,16 0,56" fill="#fff"/>
  <polyline points="0,56 600,16 1200,56" fill="none" stroke="#c4141f" stroke-width="5"/>
</svg>

</body>
</html>
```